Budget Brand Responsive Website

Flat vector style website needed for value based IT support company. looking for clean, illustration intensive based design. Current test site can be found at www.bright-mend.co.uk and holding page it www.brightmend.co.uk this will show text and services, please feel free to use placeholder text if you think we need alternative text in places. Emphasis should be on low cost support and services listed on the site, would be nice to see costs in bold images. important colors are the blue, orange and white, see holding page and attached image of an advert

It Company

```html
<!DOCTYPE html>
<html lang="en">
<head>
<meta charset="utf-8">
<title>Bright Mend – Value IT Support</title>
<link href="https://fonts.googleapis.com/css2?family=Roboto:wght@300;400;500;700&display=swap" rel="stylesheet">
<style>
:root{
  --blue:#2a5a9c;
  --blue-dark:#1c3e6e;
  --orange:#ef7d22;
  --ink:#333;
  --muted:#8a8f96;
  --line:#e2e4e7;
  --grey-bg:#f0f2f4;
  --footer:#2a2c2f;
  --footer-base:#1d1f21;
  --white:#fff;
}
*{box-sizing:border-box;margin:0;padding:0}
html,body{width:1200px;height:2460px;overflow:hidden}
body{font-family:"Roboto",Arial,sans-serif;color:var(--ink);background:var(--white)}
.site-header{height:72px;display:flex;align-items:center;justify-content:space-between;padding:0 60px;border-bottom:1px solid var(--line)}
.brand{display:flex;align-items:center;gap:10px;font-weight:700;font-size:26px;color:var(--blue);letter-spacing:.5px}
.brand-square{width:22px;height:22px;background:var(--orange)}
.main-nav{display:flex;align-items:center;gap:38px;font-size:13px;font-weight:700;color:var(--ink)}
.main-nav .active{color:var(--orange)}
.search-btn{width:30px;height:30px;border:2px solid var(--orange);border-radius:50%;display:flex;align-items:center;justify-content:center}
.hero{height:480px;position:relative;background:radial-gradient(ellipse at 50% 45%,#3d6fa3 0%,#23497a 55%,#15304f 100%)}
.hero-arrow{position:absolute;top:222px;width:36px;height:36px;border-radius:50%;background:rgba(255,255,255,.2);display:flex;align-items:center;justify-content:center}
.hero-arrow.prev{left:20px}.hero-arrow.next{right:20px}
.section-title{text-align:center;font-size:28px;font-weight:500;letter-spacing:1px}
.title-rule{width:60px;height:3px;background:var(--orange);margin:12px auto 0}
.welcome{height:208px;padding-top:34px;text-align:center}
.welcome .section-title{color:var(--blue)}
.welcome p{width:720px;margin:18px auto 0;font-size:13px;line-height:20px;color:var(--muted)}
.call-btn{display:inline-block;margin-top:18px;background:var(--orange);color:var(--white);padding:12px 30px;font-size:15px;border-radius:3px}
.call-btn strong{font-size:20px;margin-left:6px}
.services{height:400px;background:var(--grey-bg);padding-top:40px}
.services .section-title{color:var(--orange)}
.service-list{display:flex;justify-content:space-between;padding:0 90px;margin-top:44px}
.service{width:200px;text-align:center}
.service-icon{width:110px;height:110px;border-radius:50%;border:3px solid var(--orange);background:var(--white);margin:0 auto;display:flex;align-items:center;justify-content:center}
.service h3{margin-top:18px;font-size:15px;font-weight:700;color:var(--ink)}
.service p{margin-top:8px;font-size:12px;line-height:18px;color:var(--muted)}
.pricing{height:600px;padding-top:40px}
.pricing .section-title{color:var(--blue)}
.plans{display:flex;gap:20px;padding:0 120px;margin-top:44px}
.plan{flex:1;border:1px solid var(--line);height:420px;display:flex;flex-direction:column}
.plan-head{background:var(--blue);color:var(--white);text-align:center;padding:16px 10px;height:76px}
.plan-head h3{font-size:17px;font-weight:500;letter-spacing:1px}
.plan-head p{font-size:11px;margin-top:6px;opacity:.9}
.plan-rows{padding:10px 18px}
.plan-row{display:flex;justify-content:space-between;font-size:12px;color:var(--ink);padding:16px 0;border-bottom:1px solid var(--line)}
.plan-row b{font-weight:700}
.btn{display:inline-block;background:var(--orange);color:var(--white);font-size:12px;font-weight:700;padding:10px 22px;border-radius:2px}
.plan .btn{margin:auto auto 34px}
.story{height:380px;display:flex;padding:30px 100px 0;gap:60px}
.story-col{flex:1}
.story h2{font-size:24px;font-weight:500;letter-spacing:.5px}
.expect h2{color:var(--orange)}
.about h2{color:var(--blue)}
.story .rule{width:50px;height:3px;background:var(--orange);margin:10px 0 22px}
.expect-body{display:flex;gap:26px;align-items:flex-start}
.story p{font-size:12px;line-height:20px;color:var(--muted)}
.about .btn{margin-top:22px}
.site-footer{height:280px;background:var(--footer);color:#c9ccd0;display:flex;padding:36px 100px 0;gap:40px}
.foot-col{flex:1}
.foot-col h4{color:var(--white);font-size:15px;font-weight:500;letter-spacing:1px;margin-bottom:16px}
.foot-col ul{list-style:none;font-size:12px;line-height:22px}
.foot-col p{font-size:12px;line-height:20px}
.field{height:28px;background:#3a3d41;border:1px solid #4a4d52;margin-top:8px;font-size:11px;color:#8d9196;padding:6px 8px}
.foot-col .btn{margin-top:10px}
.social li{display:flex;align-items:center;gap:10px}
.social li::before{content:"";width:10px;height:10px;border-radius:50%;background:var(--orange)}
.footer-base{height:40px;background:var(--footer-base);color:#8d9196;font-size:11px;display:flex;align-items:center;justify-content:space-between;padding:0 100px}
</style>
</head>
<body>
<header class="site-header">
  <div class="brand"><span class="brand-square"></span>BRIGHT MEND</div>
  <nav class="main-nav">
    <span class="active">HOME</span><span>SUPPORT</span><span>SERVICES</span><span>ABOUT</span><span>CONTACT</span>
    <span class="search-btn"><svg width="14" height="14" viewBox="0 0 14 14"><circle cx="6" cy="6" r="4" fill="none" stroke="#ef7d22" stroke-width="2"/><line x1="9" y1="9" x2="13" y2="13" stroke="#ef7d22" stroke-width="2"/></svg></span>
  </nav>
</header>

<section class="hero" role="img" aria-label="Chalkboard illustration of business planning: management diagram, light bulb vision, organisation chart, growth chart and strategy notes">
  <span class="hero-arrow prev"><svg width="12" height="12" viewBox="0 0 12 12"><polyline points="8,1 3,6 8,11" fill="none" stroke="#fff" stroke-width="2"/></svg></span>
  <span class="hero-arrow next"><svg width="12" height="12" viewBox="0 0 12 12"><polyline points="4,1 9,6 4,11" fill="none" stroke="#fff" stroke-width="2"/></svg></span>
</section>

<section class="welcome">
  <h1 class="section-title">WELCOME BRIGHTMEND</h1>
  <div class="title-rule"></div>
  <p>We are a value focused IT support provider for small and growing businesses. Our friendly team keeps your systems running smoothly and securely, with clear pricing and no long contracts, so you can focus on what matters most to you.</p>
  <span class="call-btn">Call us today on <strong>01632 960 418</strong></span>
</section>

<section class="services">
  <h2 class="section-title">SERVICES TAILORED FOR YOU</h2>
  <div class="title-rule"></div>
  <div class="service-list">
    <div class="service">
      <div class="service-icon"><svg width="50" height="50" viewBox="0 0 50 50" fill="none" stroke="#ef7d22" stroke-width="3"><path d="M10 28 V24 a15 15 0 0 1 30 0 V28"/><rect x="6" y="26" width="8" height="12" rx="2"/><rect x="36" y="26" width="8" height="12" rx="2"/><path d="M40 38 q0 6 -10 6"/></svg></div>
      <h3>SUPPORT</h3>
      <p>Fast friendly help desk support for your whole team, ready whenever you need us.</p>
    </div>
    <div class="service">
      <div class="service-icon"><svg width="50" height="50" viewBox="0 0 50 50" fill="none" stroke="#ef7d22" stroke-width="3"><path d="M14 8 l7 8 -4 5 q4 8 12 12 l5 -4 8 7 -5 6 q-18 -2 -28 -28 z"/></svg></div>
      <h3>VOICE</h3>
      <p>Flexible phone systems with lower call rates and simple line rental for your office.</p>
    </div>
    <div class="service">
      <div class="service-icon"><svg width="50" height="50" viewBox="0 0 50 50" fill="none" stroke="#ef7d22" stroke-width="3"><circle cx="25" cy="25" r="18"/><ellipse cx="25" cy="25" rx="8" ry="18"/><line x1="7" y1="25" x2="43" y2="25"/></svg></div>
      <h3>INTERNET</h3>
      <p>Reliable broadband and fibre connections sized to suit your business at fair prices.</p>
    </div>
    <div class="service">
      <div class="service-icon"><svg width="50" height="50" viewBox="0 0 50 50" fill="none" stroke="#ef7d22" stroke-width="3"><path d="M25 6 l16 6 v12 q0 14 -16 20 q-16 -6 -16 -20 v-12 z"/><polyline points="17,25 23,31 33,19"/></svg></div>
      <h3>SECURITY</h3>
      <p>Protect your data with managed antivirus, firewall and backup from a trusted team.</p>
    </div>
  </div>
</section>

<section class="pricing">
  <h2 class="section-title">PRICING FOR OUR MOST POPULAR SERVICES</h2>
  <div class="title-rule"></div>
  <div class="plans">
    <div class="plan">
      <div class="plan-head"><h3>SUPPORT</h3><p>Unlimited Monthly Remote Support</p></div>
      <div class="plan-rows">
        <div class="plan-row"><span>Workstations</span><b>£35.00</b></div>
        <div class="plan-row"><span>Client PC</span><b>£30.00</b></div>
        <div class="plan-row"><span>Servers</span><b>£45.00</b></div>
      </div>
      <span class="btn">READ MORE</span>
    </div>
    <div class="plan">
      <div class="plan-head"><h3>VOICE</h3><p>Lower rates and call charges</p></div>
      <div class="plan-rows">
        <div class="plan-row"><span>Workstations</span><b>£20.00</b></div>
        <div class="plan-row"><span>Client PC</span><b>£15.00</b></div>
        <div class="plan-row"><span>Servers</span><b>£25.00</b></div>
      </div>
      <span class="btn">READ MORE</span>
    </div>
    <div class="plan">
      <div class="plan-head"><h3>HOSTING</h3><p>Flexible and Secure</p></div>
      <div class="plan-rows">
        <div class="plan-row"><span>Workstations</span><b>£10.00</b></div>
        <div class="plan-row"><span>Client PC</span><b>£12.00</b></div>
        <div class="plan-row"><span>Servers</span><b>£40.00</b></div>
      </div>
      <span class="btn">READ MORE</span>
    </div>
    <div class="plan">
      <div class="plan-head"><h3>CLOUD</h3><p>Reduced costs &amp; Increase Performance</p></div>
      <div class="plan-rows">
        <div class="plan-row"><span>Workstations</span><b>£18.00</b></div>
        <div class="plan-row"><span>Client PC</span><b>£16.00</b></div>
        <div class="plan-row"><span>Servers</span><b>£50.00</b></div>
      </div>
      <span class="btn">READ MORE</span>
    </div>
  </div>
</section>

<section class="story">
  <div class="story-col expect">
    <h2>WE EXCEED EXPECTATIONS</h2>
    <div class="rule"></div>
    <div class="expect-body">
      <svg width="140" height="140" viewBox="0 0 140 140" role="img" aria-label="75 percent">
        <circle cx="70" cy="70" r="55" fill="none" stroke="#e2e4e7" stroke-width="16"/>
        <circle cx="70" cy="70" r="55" fill="none" stroke="#ef7d22" stroke-width="16" stroke-dasharray="259.2 345.6" transform="rotate(-90 70 70)"/>
        <text x="70" y="80" text-anchor="middle" font-family="Roboto, Arial, sans-serif" font-size="30" font-weight="700" fill="#ef7d22">75%</text>
      </svg>
      <p>Unlike traditional IT support companies and other Managed Service Providers we do not charge per hour or lock you into long contracts. We understand that our clients want value, so every plan is built to be simple and fair. Over 75% of our clients have their issues resolved on the first call, and most within the hour.</p>
    </div>
  </div>
  <div class="story-col about">
    <h2>ABOUT BRIGHT MEND</h2>
    <div class="rule"></div>
    <p>Bright Mend is a value based managed service provider offering IT support, voice, hosting and cloud services to small businesses. Our aim is to give every client the same quality of service normally reserved for large firms, at a price that makes sense. We have a growing team of engineers with years of experience across all major platforms, and we pride ourselves on being approachable, honest and quick to respond.</p>
    <span class="btn">READ MORE</span>
  </div>
</section>

<footer class="site-footer">
  <div class="foot-col">
    <h4>HARBOURLINE</h4>
    <ul><li>Home</li><li>Support</li><li>Services</li><li>About</li><li>Contact</li></ul>
  </div>
  <div class="foot-col">
    <h4>CONTACT US</h4>
    <p>Harbour Road, Westcliff<br>Essex SS0 7AB</p>
    <p style="margin-top:10px">info@brightmend.co.uk<br>+44 (0) 1632 960 418</p>
  </div>
  <div class="foot-col">
    <h4>SIGN TO NEWSLETTER</h4>
    <p>Join our newsletter to receive our latest offers, tips and news straight to your inbox.</p>
    <div class="field">Name</div>
    <div class="field">Email</div>
    <span class="btn">SUBSCRIBE</span>
  </div>
  <div class="foot-col">
    <h4>FOLLOW US</h4>
    <ul class="social"><li>Friendbook</li><li>Chirper</li><li>ViewTube</li><li>Snapgram</li></ul>
  </div>
</footer>
<div class="footer-base">
  <span>© 2017 Bright Mend Ltd trading as Bright Mend Computing · Company Registration No: 01234567</span>
  <span>1 / 6</span>
</div>
</body>
</html>
```